Brindle Haulage Heavy Goods Transport web design

I have a client who requires a new web site design.
They are Brindle Haulage in the UK.
They have a current site which needs updating with a fresh look and feel using modern design ideas.
Their current site is brindlehaulage.co.uk
I will use your design to build a new CMS site for them using Django.
I only require the layered PSD files, main page design plus a sub page showing navigation changes and layout changes between pages.
The site needs to have the same sections as the current site plus:
1) Proof of delivery downloads system (customer logs in to access their delivery documents).
2) CMS system will allow them to add pages so the menu system needs to be designed such that it can expand.
3) A contact page with a contact form and a Google map will be used.
4) No flash.
5) Slideshow banners (using JQuery will be used).
I like the following type of designs:
www.billoranta.example/pricing.html
www.ledgerpine.example/
vantro.example/features
navkitra.example/
I am looking for a designer to work with me designing other web design projects as well so this project will be used as a test bed for us working together.
The budget for our client designs is between £120 and £200 depending on functionality requirements. This site has a budget of £150.
Please submit your quotes by email to tmarsh@oakvale-studio.example
Target Market(s)
Industrial business customers
Industry/Entity Type
Build
Look and feel

```html
<!DOCTYPE html>
<html lang="en">
<head>
<meta charset="utf-8">
<title>Brindle Haulage Services – Home</title>
<link href="https://fonts.googleapis.com/css2?family=Ubuntu:wght@400;500&display=swap" rel="stylesheet">
<style>
  :root {
    --forest: #022d07;
    --forest-text: #0b3a10;
    --orange: #f6a547;
    --orange-light: #ffd699;
    --orange-text: #f3a33b;
    --mint: #e3ede5;
    --slate: #a9aeac;
    --ink: #1e1e1e;
    --white: #ffffff;
  }
  * { box-sizing: border-box; margin: 0; padding: 0; }
  html, body { width: 1195px; height: 1200px; overflow: hidden; }
  body { position: relative; background: var(--white); font-family: "Ubuntu", sans-serif; color: var(--ink); }

  .site-header { position: absolute; left: 0; top: 0; width: 1195px; height: 127px; background: var(--forest); }
  .brand { position: absolute; left: 54px; top: 42px; display: flex; align-items: center; gap: 10px; }
  .brand-mark { width: 22px; height: 22px; background: var(--orange); }
  .brand-name { font-size: 27px; font-weight: 500; color: var(--orange); }
  .account-links { position: absolute; right: 47px; top: 10px; font-size: 13.5px; color: var(--white); }
  .account-links .welcome { color: var(--orange-text); }
  .account-links .sep { color: var(--orange-text); margin: 0 6px; }
  .contact-lines { position: absolute; right: 47px; top: 58px; text-align: right; font-size: 13.5px; line-height: 19.5px; color: var(--white); }

  .main-nav { position: absolute; left: 0; top: 127px; width: 1195px; height: 48px; background: linear-gradient(var(--orange-light), var(--orange)); }
  .main-nav a { position: absolute; top: 14px; font-size: 17px; color: var(--forest-text); text-decoration: none; }
  .main-nav a.active { left: 40px; top: 0; width: 117px; height: 44px; line-height: 44px; text-align: center; background: var(--forest); color: var(--orange-text); }

  .band { position: absolute; left: 0; top: 494px; width: 1195px; height: 483px; background: var(--mint); }

  .hero { position: absolute; left: 39px; top: 191px; width: 1119px; height: 373px; background: var(--slate); overflow: hidden; }
  .hero-photo { position: absolute; left: 0; top: 0; width: 660px; height: 373px; background: linear-gradient(90deg, rgba(169,174,172,0) 88%, var(--slate) 100%), linear-gradient(180deg, #d9dcdd 0%, #8e9193 55%, #6f7174 100%); }
  .hero-copy { position: absolute; left: 685px; top: 52px; width: 400px; }
  .hero-copy h1 { font-size: 27.5px; font-weight: 400; line-height: 30.5px; color: var(--forest-text); }
  .hero-copy p { margin-top: 22px; width: 385px; font-size: 16.3px; line-height: 24px; color: #2a2a2a; }
  .btn { display: block; position: absolute; background: linear-gradient(var(--orange-light), var(--orange)); color: #1d1d1d; text-decoration: none; text-align: center; border-radius: 20px; }
  .hero-btn { left: 977px; top: 502px; width: 132px; height: 34px; line-height: 34px; font-size: 15px; }

  .feature { position: absolute; top: 584px; width: 346px; }
  .feature-photo { width: 346px; height: 150px; }
  .feature h2 { margin: 11px 0 0 8px; font-size: 19px; font-weight: 500; color: var(--forest-text); }
  .feature p { margin: 3px 0 0 8px; width: 322px; font-size: 14px; line-height: 19.4px; color: #1e1e1e; }
  .feature .btn { top: 324px; width: 83px; height: 23px; line-height: 23px; font-size: 10.5px; }

  .partners { position: absolute; left: 0; top: 994px; width: 1195px; height: 110px; }
  .partner { position: absolute; }

  .site-footer { position: absolute; left: 40px; top: 1118px; width: 1119px; height: 82px; background: var(--forest); color: var(--white); font-size: 12px; text-align: center; line-height: 110px; }
</style>
</head>
<body>
  <header class="site-header">
    <div class="brand"><span class="brand-mark"></span><span class="brand-name">Brindle Haulage</span></div>
    <div class="account-links"><span class="welcome">Welcome Guest</span><span class="sep">|</span>Join Now<span class="sep">|</span>Login</div>
    <div class="contact-lines">
      Telephone : 01632 960466<br>
      Fax &nbsp;: 01632 960915<br>
      E-Mail : info@brindlehaulage.co.uk
    </div>
  </header>

  <nav class="main-nav">
    <a class="active" href="#">Home</a>
    <a href="#" style="left:178px">About Us</a>
    <a href="#" style="left:306px">Culture</a>
    <a href="#" style="left:419px">The Team</a>
    <a href="#" style="left:551px">Depots</a>
    <a href="#" style="left:663px">Contact Us</a>
    <a href="#" style="left:804px">Notice Board</a>
    <a href="#" style="left:960px">Customers Feedback</a>
  </nav>

  <div class="band"></div>

  <section class="hero">
    <div class="hero-photo" role="img" aria-label="Two heavy goods truck cabs, one grey and one red, under a cloudy sky"></div>
    <div class="hero-copy">
      <h1>Brindle Haulage Services (Midlands) Ltd we are a family owned and run Transport and Distribution company.</h1>
      <p>we believe that by developing our staff through People Growth Standard and an ongoing driver assessment program we can maintain a leading edge with in the market place.</p>
    </div>
  </section>
  <a class="btn hero-btn" href="#">Read more</a>

  <article class="feature" style="left:61px">
    <div class="feature-photo" role="img" aria-label="Mechanics servicing a green truck in the workshop" style="background:linear-gradient(90deg,#6b5a4c,#3f6b3a)"></div>
    <h2>Culture</h2>
    <p>We are committed to providing our customers with excellent service encompassing adaptable solutions and using our ability to adjust operations to reflect the ever changing business environment. We strive for continual improvement and innovation.</p>
    <a class="btn" href="#" style="left:116px">Read more</a>
  </article>

  <article class="feature" style="left:425px">
    <div class="feature-photo" role="img" aria-label="Three drivers standing in front of a company truck" style="background:linear-gradient(90deg,#2e5a2c,#5f7a4a 60%,#b9d24a)"></div>
    <h2>The Team</h2>
    <p>We are committed to providing our customers with excellent service encompassing adaptable solutions and using our ability to adjust operations to reflect the ever changing business environment. We strive for continual improvement and innovation.</p>
    <a class="btn" href="#" style="left:137px">Read more</a>
  </article>

  <article class="feature" style="left:791px">
    <div class="feature-photo" role="img" aria-label="Red curtain-sided lorry parked outside a depot" style="background:linear-gradient(180deg,#c6d8ee 0%,#9aa3ab 45%,#c8412a 60%,#7c8a6a 100%)"></div>
    <h2>Depots</h2>
    <p>We are committed to providing our customers with excellent service encompassing adaptable solutions and using our ability to adjust operations to reflect the ever changing business environment. We strive for continual improvement and innovation.</p>
    <a class="btn" href="#" style="left:140px">Read more</a>
  </article>

  <section class="partners" aria-label="Accreditations and partners">
    <div class="partner" role="img" aria-label="Accreditation badge" style="left:69px;top:9px;width:136px;height:96px;background:var(--forest)"></div>
    <div class="partner" role="img" aria-label="Trade association badge" style="left:240px;top:9px;width:112px;height:98px;border-radius:50%;background:#2b2b2b"></div>
    <div class="partner" role="img" aria-label="Member crest badge" style="left:388px;top:3px;width:85px;height:103px;background:#123d12"></div>
    <div class="partner" role="img" aria-label="Partner badge" style="left:512px;top:0;width:145px;height:110px;background:#eeeeee"></div>
    <div class="partner" role="img" aria-label="Partner badge" style="left:699px;top:17px;width:70px;height:70px;border-radius:50%;background:#f07c1c"></div>
    <div class="partner" role="img" aria-label="Partner badge" style="left:952px;top:22px;width:179px;height:60px;background:#1f2a8a"></div>
  </section>

  <footer class="site-footer">© Copyright 2012 Brindle Haulage Services (Midlands), All rights reserved</footer>
</body>
</html>
```